Psychiatric Office Needs a Website- 1st Time Ever!

Been in practice since 2003 with no website, but finally ready to dive in. We are Maplecrest Behavioral Healthcare, a mental health outpatient practice based in Fayetteville, Georgia that sees diverse individuals and families from childhood to advanced age for a variety of conditions. We've grown by word of mouth and referral but would now like to have a digital footprint. Be the pioneer of our website and we will be sure to share. We would like to see designs that are modern, animated, fairly colorful, easy to read, and caters to all ages. Also, we would like the design to take the whole page (not be centered) and can be viewed well on phone/tablet. Please see our outline for more information. Our motto/slogan is: Maplecrest Behavioral Healthcare- A step forward in your wellness journey, so the design should try to reflect that.
Updates

Project Deadline Extended
Reason: site in progress

Target Market(s)

Children through elderly

Industry/Entity Type

Medical

Logo Text

Stepping forward in your wellness journey

Number of Pages Required

1 page

Colors

Designer to choose colors to be used in the design.

Requirements
Must have
• Animation or moving pictures.
• Color.
• Concise.
• User friendly
• Diversity in the stock photos

```html
<!DOCTYPE html>
<html lang="en">
<head>
<meta charset="utf-8">
<title>Maplecrest Behavioral Healthcare</title>
<link href="https://fonts.googleapis.com/css2?family=Asap:ital,wght@0,400;0,600;0,700;1,400&family=Lato:wght@400;700&display=swap" rel="stylesheet">
<style>
:root{
  --blue:#2e9ad8;
  --blue-dark:#1f7fb9;
  --green:#7cb342;
  --green-soft:#9cc96b;
  --charcoal:#333536;
  --footer:#3b3f44;
  --ink:#444;
  --muted:#777;
  --white:#fff;
}
*{box-sizing:border-box;margin:0;padding:0}
html,body{width:1200px;height:3750px;overflow:hidden}
body{position:relative;font-family:"Lato",sans-serif;color:var(--ink);background:var(--white)}
.abs{position:absolute}
h1,h2,h3,.heading{font-family:"Asap",sans-serif;font-weight:400}

/* top bar */
.topbar{left:0;top:0;width:1200px;height:45px;background:var(--charcoal)}
.social-dot{top:12px;width:20px;height:20px;border-radius:50%;background:#9a9c9e}
.patient-login{left:918px;top:0;width:204px;height:45px;background:var(--green);color:#fff;font-size:17px;display:flex;align-items:center;justify-content:center;gap:10px}

/* header */
.header{left:0;top:45px;width:1200px;height:130px;background:#fff}
.brand{left:70px;top:70px;display:flex;align-items:center;gap:12px}
.brand-mark{width:60px;height:60px;border-radius:50%;border:4px solid var(--blue)}
.brand-name{font-family:"Asap",sans-serif;font-size:20px;color:var(--blue);line-height:1.15;width:150px}
.info{top:80px;display:flex;gap:14px;align-items:center;font-size:14.5px;color:#555;line-height:1.45}
.info-icon{width:38px;height:38px;border:2px solid var(--green);border-radius:4px;flex:none}

/* nav */
.nav{left:0;top:175px;width:1200px;height:55px;background:var(--blue);display:flex;padding-left:77px}
.nav a{color:#fff;text-decoration:none;font-family:"Asap",sans-serif;font-size:21px;padding:0 22px;line-height:55px}
.nav a.active{background:var(--green)}

/* hero */
.hero-photo{left:0;top:230px;width:1200px;height:575px;background:linear-gradient(120deg,#4a5a66 0%,#8a9aa4 35%,#c9d3d8 55%,#6e7f88 100%)}
.hero-panel{left:688px;top:230px;width:512px;height:575px;background:rgba(124,179,66,.88)}
.hero-frame{left:708px;top:250px;width:462px;height:533px;border:2px solid rgba(255,255,255,.85);text-align:center;color:#fff}
.hero-mark{margin:78px auto 0;width:104px;height:104px;border-radius:50%;background:#fff}
.hero-title{font-family:"Asap",sans-serif;font-style:italic;font-size:40px;line-height:1.15;margin-top:20px}
.hero-tag{font-size:18px;margin-top:12px;font-style:italic}
.btn{display:inline-block;background:var(--blue);color:#fff;font-size:19px;padding:14px 30px;text-transform:uppercase}
.hero-frame .btn{margin-top:28px}
.hero-arrow{left:640px;top:470px;width:48px;height:78px;background:#fff;border-radius:40px 0 0 40px}

/* about */
.about{left:0;top:805px;width:1200px;height:353px;background:var(--blue);color:#fff;text-align:center}
.section-title{font-size:43px}
.divider{display:flex;align-items:center;justify-content:center;gap:10px;margin-top:10px}
.divider span{width:120px;height:1px;background:currentColor;opacity:.7}
.divider i{width:18px;height:18px;border:1.5px solid currentColor;border-radius:50%}
.about p{width:980px;margin:20px auto 0;font-size:14.5px;line-height:1.85}
.about-tab{left:1015px;width:105px;height:40px}
.chevron{left:572px;top:1130px;width:56px;height:56px;border-radius:50%;background:#fff;display:flex;align-items:center;justify-content:center}

/* services */
.services{left:0;top:1158px;width:1200px;height:585px;background:linear-gradient(135deg,#8fb96a,#6fa14a 50%,#8dbb6e)}
.services .section-title{position:absolute;top:68px;width:1200px;text-align:center;color:#fff;font-size:45px}
.service{width:247px;height:165px;border:3px solid rgba(255,255,255,.45);color:#fff;font-family:"Asap",sans-serif;font-size:17px;text-align:center;display:flex;align-items:center;justify-content:center;padding:0 12px}
.service.featured{background:rgba(46,154,216,.85);flex-direction:column;justify-content:flex-start;padding-top:20px;height:347px}
.service.featured .mark{width:80px;height:80px;border-radius:50%;background:#fff;margin-bottom:14px}
.service.featured p{font-family:"Lato",sans-serif;font-size:13.5px;line-height:1.5;margin-top:12px}
.service .label-bar{background:var(--blue);padding:8px 12px;width:100%}

/* vision mission */
.vm{left:0;top:1743px;width:1200px;height:390px;background:var(--charcoal);color:#fff}
.vm-col{top:55px;width:375px}
.vm-col h2{font-size:36px;text-transform:uppercase;border-bottom:1px solid #666;padding-bottom:8px;width:120px}
.vm-col p{font-size:14.5px;line-height:1.75;margin-top:14px}
.vm-col .btn{margin-top:22px;font-size:18px;padding:14px 38px}
.vm-visual{left:428px;top:-5px;width:344px;height:400px;border-radius:50%/45%;background:#cfd3d5}
.vm-photo{left:450px;top:20px;width:300px;height:330px;border-radius:50%;background:radial-gradient(circle,#8e9294,#3c4043)}

/* conditions */
.conditions{left:0;top:2133px;width:1200px;height:680px;overflow:hidden}
.conditions .section-title{position:absolute;top:60px;width:1200px;text-align:center;color:var(--blue);font-size:39px;text-transform:uppercase}
.conditions .divider{position:absolute;top:115px;width:1200px;color:#555}
.circle{width:240px;height:240px;border-radius:50%;border:6px solid var(--blue);box-shadow:0 6px 14px rgba(0,0,0,.35);overflow:hidden}
.circle .label{position:absolute;left:0;top:120px;width:100%;height:44px;background:rgba(124,179,66,.85);color:#fff;font-size:17px;display:flex;align-items:center;justify-content:center;text-align:center;line-height:1.1}
.circle.text{background:#1d1f20;color:#fff;text-align:center;padding:40px 28px 0}
.circle.text h3{font-size:20px}
.circle.text p{font-size:14px;line-height:1.45;margin-top:8px}

/* faq & news */
.faq{left:80px;top:2860px;width:520px}
.faq h2,.news h2{font-size:36px;color:var(--blue)}
.faq-item{border:1px solid #ddd;margin-top:-1px;padding:8px 14px;font-size:19px;color:var(--blue);display:flex;gap:12px;align-items:center}
.faq-item b{color:var(--green);font-size:24px;line-height:1}
.faq-open{border:1px solid #ddd;padding:0}
.faq-open .faq-item{border:none;border-bottom:1px solid #ddd}
.faq-open p{font-size:12.5px;line-height:1.6;padding:10px 14px;color:#555}
.faq-first{margin-top:16px}
.news{left:667px;top:2860px;width:460px}
.news-item{display:flex;gap:16px;margin-top:22px}
.news-thumb{width:118px;height:108px;flex:none}
.news-item h3{font-size:19px;color:var(--blue)}
.news-date{font-size:12px;color:var(--green);margin-top:4px}
.news-item p{font-size:14.5px;line-height:1.5;margin-top:4px}
.read-more{font-size:13px;color:var(--blue);margin-top:8px;letter-spacing:.5px}

/* footer */
.footer{left:0;top:3280px;width:1200px;height:470px;background:var(--footer);color:#fff}
.footer-mark{left:540px;top:-25px;width:120px;height:120px;border-radius:50%;background:#fff;border:4px solid #d8dadc;display:flex;align-items:center;justify-content:center;text-align:center;font-family:"Asap",sans-serif;font-size:13px;color:var(--blue);padding:10px;line-height:1.15}
.fcol{top:120px}
.fcol h4{font-family:"Asap",sans-serif;font-weight:400;font-size:17px;color:var(--blue);letter-spacing:1px;text-transform:uppercase;margin-bottom:14px}
.links li{list-style:none;font-size:14px;line-height:2.15}
.links li.current{color:var(--green)}
.contact-row{display:flex;gap:16px;font-size:14px;line-height:1.55;margin-bottom:14px}
.contact-row i{width:18px;height:18px;border:2px solid var(--blue);border-radius:50%;flex:none;margin-top:2px}
.newsletter p{font-size:14.5px;line-height:1.6;width:240px}
.email-field{margin-top:26px;width:250px;height:44px;background:#fff;color:#333;font-size:13px;padding:14px 12px}
.subscribe{margin-top:12px;width:188px;height:50px;background:var(--green);color:#fff;font-size:19px;letter-spacing:1px;display:flex;align-items:center;justify-content:center}
.footer-about{font-size:16.5px;line-height:1.55;width:220px}
.square{width:44px;height:44px;background:var(--green);display:inline-block;margin-right:10px}
</style>
</head>
<body>

<!-- top bar -->
<div class="abs topbar">
  <span class="abs social-dot" style="left:78px"></span>
  <span class="abs social-dot" style="left:110px"></span>
  <span class="abs social-dot" style="left:142px"></span>
  <span class="abs social-dot" style="left:174px"></span>
  <div class="abs patient-login">
    <svg width="18" height="18" viewBox="0 0 18 18"><rect x="3" y="8" width="12" height="9" fill="#fff"/><path d="M5 8V5a4 4 0 0 1 8 0v3" stroke="#fff" stroke-width="2" fill="none"/></svg>
    PATIENT LOGIN
  </div>
</div>

<!-- header -->
<header class="abs header"></header>
<div class="abs brand">
  <span class="brand-mark"></span>
  <span class="brand-name">Maplecrest Behavioral Healthcare</span>
</div>
<div class="abs info" style="left:290px">
  <span class="info-icon"></span>
  <span>Monday - Friday : 10.00 A.M to 8.00 P.M<br>Saturday and Sunday - Closed</span>
</div>
<div class="abs info" style="left:620px">
  <span class="info-icon"></span>
  <span>+1-555-010-2040<br>hello@maplecresthealth.example</span>
</div>
<div class="abs info" style="left:888px">
  <span class="info-icon"></span>
  <span>Maplecrest Behavioral Avenue<br>Fayette Row</span>
</div>

<!-- nav -->
<nav class="abs nav">
  <a class="active">Home</a><a>About Us</a><a>Services</a><a>Conditions We Treat</a><a>New Patients</a><a>Contact Us</a>
</nav>

<!-- hero -->
<div class="abs hero-photo" role="img" aria-label="Photo of a clinician and a colleague reviewing work at a laptop in a bright office"></div>
<div class="abs hero-panel"></div>
<div class="abs hero-arrow"><svg width="48" height="78" viewBox="0 0 48 78"><path d="M32 24 L20 39 L32 54" stroke="#7cb342" stroke-width="3" fill="none"/></svg></div>
<div class="abs hero-frame">
  <div class="hero-mark"></div>
  <h1 class="hero-title">Maplecrest Behavioral<br>Healthcare</h1>
  <p class="hero-tag">A step forward in your wellness journey</p>
  <span class="btn">Contact us</span>
</div>

<!-- about -->
<section class="abs about">
  <h2 class="section-title" style="margin-top:60px">About <b style="font-weight:700">MAPLECREST BEHAVIORAL</b> Healthcare</h2>
  <div class="divider"><span></span><i></i><span></span></div>
  <p>Lorem Ipsum is simply dummy text of the printing and typesetting industry. Lorem Ipsum has been the industry's standard dummy text ever since the 1500s, when an unknown printer took a galley of type and scrambled it to make a type specimen book. It has survived not only five centuries, but also the leap into electronic typesetting, remaining essentially unchanged. It was popularised in the 1960s with the release of Typeline sheets containing Lorem Ipsum passages, and more recently with desktop publishing software like Pagecraft Studio including versions of Lorem Ipsum.</p>
  <div class="abs about-tab" style="top:195px;background:#3d5a6c"></div>
  <div class="abs about-tab" style="top:240px;background:#3aa6e0"></div>
  <div class="abs about-tab" style="top:285px;background:var(--green)"></div>
</section>

<!-- services -->
<section class="abs services" role="img" aria-label="Soft green backdrop photo of a smiling family">
  <h2 class="section-title">services</h2>
  <div class="divider" style="position:absolute;top:125px;width:1200px;color:#fff"><span></span><i></i><span></span></div>
  <div class="abs service featured" style="left:80px;top:170px">
    <span class="mark"></span>
    Disability and<br>work-related reports
    <p>Lorem Ipsum is simply dummy text of the printing and typesetting industry. Lorem Ipsum has been the industry's standard dummy text ever since the 1500s.</p>
  </div>
  <div class="abs service" style="left:343px;top:170px;background:#8a7a6a;align-items:flex-end;padding:0 0 28px" role="img" aria-label="Photo of a clinician talking with a patient"><span class="label-bar">Diagnostic evaluation and treatment</span></div>
  <div class="abs service" style="left:608px;top:170px;background:#8c8078" role="img" aria-label="Photo of a counselling session">Psychopharmacology</div>
  <div class="abs service" style="left:873px;top:170px;background:#7d7f80" role="img" aria-label="Photo of a pre-surgical consultation">Bariatric pre-surgical consultation</div>
  <div class="abs service" style="left:343px;top:352px;background:#9a8e6e" role="img" aria-label="Photo of a family gathered together">Developmental disabilities</div>
  <div class="abs service" style="left:608px;top:352px;background:#444a4e" role="img" aria-label="Photo of a support group">Substance abuse assesments</div>
  <div class="abs service" style="left:873px;top:352px;background:#8a7a64" role="img" aria-label="Photo of parents with a young child">Early childhood Assessments</div>
</section>
<div class="abs chevron"><svg width="26" height="16" viewBox="0 0 26 16"><path d="M3 3 L13 12 L23 3" stroke="#7cb342" stroke-width="4" fill="none"/></svg></div>

<!-- vision & mission -->
<section class="abs vm">
  <div class="abs vm-visual"></div>
  <div class="abs vm-photo" role="img" aria-label="Illustration of a glowing brain hovering above an open hand"></div>
  <div class="abs vm-col" style="left:80px">
    <h2>Vision</h2>
    <p>Lorem Ipsum is simply dummy text of the printing and typesetting industry. Lorem Ipsum has been the industry's standard dummy text ever since the 1500s, when an unknown printer took a galley of type and scrambled it to make a type specimen book.</p>
    <span class="btn">Read more</span>
  </div>
  <div class="abs vm-col" style="left:795px">
    <h2>Mission</h2>
    <p>Lorem Ipsum is simply dummy text of the printing and typesetting industry. Lorem Ipsum has been the industry's standard dummy text ever since the 1500s, when an unknown printer took a galley of type and scrambled it to make a type specimen book.</p>
    <span class="btn">Read more</span>
  </div>
</section>

<!-- conditions -->
<section class="abs conditions">
  <svg class="abs" style="left:0;top:0" width="1200" height="680" viewBox="0 0 1200 680">
    <rect width="1200" height="680" fill="#6aacd4"/>
    <polygon points="0,0 1200,0 1200,680 420,680 0,230" fill="#a6cd86"/>
    <polygon points="0,0 120,0 0,90" fill="#3f9fd8"/>
    <polygon points="700,680 1200,330 1200,680" fill="#6aacd4"/>
  </svg>
  <h2 class="section-title">Conditiond we treat</h2>
  <div class="divider"><span></span><i></i><span></span></div>
  <div class="abs circle" style="left:213px;top:172px;background:#8a6a52" role="img" aria-label="Photo of a woman, representing mood disorders"><span class="label">Mood Disorders</span></div>
  <div class="abs circle" style="left:480px;top:172px;background:#8aa07a" role="img" aria-label="Photo of a woman outdoors, representing anxiety disorders"><span class="label">Anxiety Disorders</span></div>
  <div class="abs circle" style="left:743px;top:172px;background:#b59a5a" role="img" aria-label="Photo of a family outdoors, representing psychotic disorders"><span class="label">Psychotic Disorders</span></div>
  <div class="abs circle" style="left:338px;top:402px;background:#8e7c6c" role="img" aria-label="Photo of a parent and child, representing common disorders of childhood"><span class="label">Common Disorders<br>of Childhood</span></div>
  <div class="abs circle text" style="left:623px;top:402px">
    <h3>Lorem Ipsum</h3>
    <p>Lorem Ipsum is simply dummy text of the printing and typesetting industry. Lorem Ipsum has been the industry's standard.</p>
  </div>
</section>

<!-- faq -->
<section class="abs faq">
  <h2>FAQ</h2>
  <div class="faq-open faq-first">
    <div class="faq-item"><b>&minus;</b>What do I need to bring with me to my first visit?</div>
    <p>Lorem Ipsum is simply dummy text of the printing and typesetting industry. Lorem Ipsum has been the industry's standard dummy text ever since the 1500s. It has survived not only five centuries, but also the leap into electronic typesetting, remaining essentially unchanged.</p>
  </div>
  <div class="faq-item"><b>+</b>How long do I have to wait to be seen?</div>
  <div class="faq-item"><b>+</b>Why is my child not doing well in school?</div>
  <div class="faq-item"><b>+</b>What typs of insurance do you accept?</div>
</section>

<!-- news -->
<section class="abs news">
  <h2>LATEST NEWS</h2>
  <div class="news-item">
    <div class="news-thumb" style="background:#8aa0b4" role="img" aria-label="Photo of a thoughtful young girl"></div>
    <div>
      <h3>Lorem Ipsum is simply dummy text</h3>
      <div class="news-date">10 JULY 2016</div>
      <p>Lorem Ipsum is simply dummy text of the printing and typesetting industry.....</p>
      <div class="read-more">READ MORE &nbsp;&raquo;</div>
    </div>
  </div>
  <div class="news-item" style="margin-top:44px">
    <div class="news-thumb" style="background:#a89a86" role="img" aria-label="Photo of children studying in a classroom"></div>
    <div>
      <h3>Lorem Ipsum is simply dummy text</h3>
      <div class="news-date">10 JULY 2016</div>
      <p>Lorem Ipsum is simply dummy text of the printing and typesetting industry.....</p>
      <div class="read-more">READ MORE &nbsp;&raquo;</div>
    </div>
  </div>
</section>

<!-- footer -->
<footer class="abs footer">
  <div class="abs footer-mark">Maplecrest Behavioral Healthcare</div>
  <div class="abs fcol" style="left:80px">
    <h4>Useful links</h4>
    <ul class="links">
      <li class="current">&raquo; Home</li><li>&raquo; About Us</li><li>&raquo; Services</li><li>&raquo; Conditions We Treat</li><li>&raquo; New Patients</li><li>&raquo; Contact Us</li>
    </ul>
  </div>
  <div class="abs fcol" style="left:345px">
    <h4>Get in touch</h4>
    <div class="contact-row"><i></i><span><span style="color:var(--blue)">Orchard Lane Practice</span><br>42 Willow Bend Road<br>Fayetteville, GA</span></div>
    <div class="contact-row"><i></i><span>+1 555 010 2041<br>+1 555 010 2042</span></div>
    <div class="contact-row"><i></i><span>office@maplecresthealth.example</span></div>
  </div>
  <div class="abs fcol newsletter" style="left:610px">
    <h4>Newsletter</h4>
    <p>Would you like to receive exclusive access to articles, white papers and our regular monthly newsletter?</p>
    <div class="email-field">Enter Email *</div>
    <div class="subscribe">SUBSCRIBE</div>
  </div>
  <div class="abs fcol" style="left:898px;top:118px">
    <p class="footer-about">Lorem Ipsum is simply dummy text of the printing and typesetting industry. Lorem Ipsum has been the industry's standard dummy text ever since the 1500s.</p>
    <div style="margin-top:42px;padding-left:22px"><span class="square"></span><span class="square"></span><span class="square"></span></div>
  </div>
</footer>

</body>
</html>
```